holloway paving service

Needs to have phone number 0418259730 and email markholloway@brightmail.com.au.
ABN 62318470915
name mark holloway

For all your concreting solutions
Excavation
Exposed & colour concrete
House & shed slabs
Driveways
Landing & steps

Contact Information for Business Card

ph 0418259730
email markholloway@brightmail.com.au.
ABN 62318470915
name mark holloway

```html
<!DOCTYPE html>
<html lang="en">
<head>
<meta charset="utf-8">
<title>Holloway Paving Service – Business Card</title>
<link rel="stylesheet" href="https://fonts.googleapis.com/css2?family=Roboto:wght@400;500;700&display=swap">
<style>
  :root {
    --page-bg: #e4e2df;
    --card-bg: #f7f7f6;
    --charcoal: #3a3a3c;
    --charcoal-soft: #5a5a5d;
    --orange: #e0441f;
    --orange-deep: #c5361a;
    --text-dark: #2b2b2b;
    --text-mid: #444444;
  }
  * { margin: 0; padding: 0; box-sizing: border-box; }
  html, body {
    width: 1200px; height: 969px; overflow: hidden;
    background: var(--page-bg);
    font-family: "Roboto", Arial, sans-serif;
  }
  .business-card {
    position: absolute; left: 100px; top: 200px;
    width: 1000px; height: 568px;
    background: var(--card-bg);
    box-shadow: 0 10px 30px rgba(0,0,0,0.18);
    overflow: hidden;
  }
  .card-shapes { position: absolute; inset: 0; }
  .brand {
    position: absolute; left: 100px; top: 228px;
    display: flex; align-items: center;
  }
  .brand-square {
    width: 58px; height: 58px; background: var(--charcoal);
    margin-right: 22px;
  }
  .brand-divider {
    width: 2px; height: 100px; background: var(--orange); margin-right: 10px;
  }
  .brand-text { display: flex; flex-direction: column; gap: 6px; }
  .brand-name {
    font-weight: 700; font-size: 21px; color: var(--orange);
    letter-spacing: 0.3px; text-transform: uppercase;
  }
  .brand-phone {
    font-weight: 700; font-size: 17px; color: var(--orange);
    letter-spacing: 1px; padding-left: 70px;
  }
  .contact {
    position: absolute; left: 558px; top: 196px;
  }
  .contact-name {
    font-weight: 700; font-size: 36px; color: var(--orange);
    text-transform: uppercase; letter-spacing: 0.3px; line-height: 1.1;
  }
  .contact-line {
    font-size: 24px; color: var(--text-dark); margin-top: 12px; line-height: 1.1;
  }
  .services {
    position: absolute; left: 0; right: 0; top: 428px;
    text-align: center; font-size: 24px; color: var(--text-mid); line-height: 1.25;
  }
  .services .dot {
    display: inline-block; width: 8px; height: 8px; background: var(--orange);
    transform: rotate(45deg); margin: 0 10px; vertical-align: middle;
  }
</style>
</head>
<body>
  <div class="business-card">
    <svg class="card-shapes" viewBox="0 0 1000 568" width="1000" height="568" aria-hidden="true">
      <polygon points="0,0 1000,0 1000,103 500,28 0,103" fill="var(--charcoal)"/>
      <polygon points="420,0 580,0 500,26" fill="var(--charcoal-soft)"/>
      <polygon points="0,462 500,562 1000,462 1000,568 0,568" fill="var(--charcoal)"/>
      <polygon points="0,472 500,568 1000,472 1000,568 0,568" fill="var(--orange)"/>
      <polygon points="0,520 500,568 0,568" fill="var(--orange-deep)" opacity="0.5"/>
    </svg>

    <div class="brand">
      <div class="brand-square"></div>
      <div class="brand-divider"></div>
      <div class="brand-text">
        <span class="brand-name">Holloway Paving Service</span>
        <span class="brand-phone">0418259730</span>
      </div>
    </div>

    <div class="contact">
      <div class="contact-name">Mark Holloway</div>
      <div class="contact-line">markholloway@brightmail.com.au</div>
      <div class="contact-line">ABN 62318470915</div>
    </div>

    <div class="services">
      <div>Excavation<span class="dot"></span>Exposed &amp; colour concrete<span class="dot"></span>House &amp; shed slabs</div>
      <div>Driveways<span class="dot"></span>Landing &amp; steps</div>
    </div>
  </div>
</body>
</html>
```